Brightway Haul & Upkeep Services, are a company that offers a 'one stop shop' pre-move clean up a

I have already selected a logo which I would like on the front of the business cards along with phone numbers, web address and email which are:
0487650392
www.brightwayhaul.com.au
brightwayhaulandupkeep@mailbox.example

On the back of the card I would like to list some of the types of service we offer (clean - move - repairs/maintenance) which are:
CLEAN - windows, gutters, solar panels, driveways/paths, carpets.
MOVE - Small/medium size house/office moves, large item pick-up & delivery, yard clean-up and removal.
General maintenance and repairs.

I would like the blue logo on a gray background.

Thanks

```html
<!DOCTYPE html>
<html lang="en">
<head>
<meta charset="utf-8">
<title>Brightway Haul &amp; Upkeep Services – Business Card</title>
<link rel="stylesheet" href="https://fonts.googleapis.com/css2?family=Titillium+Web:wght@700&family=Source+Sans+3:wght@400;600;700&display=swap">
<style>
  :root {
    --page: #e9e7e4;
    --card-grey: #c3c3c3;
    --brand-blue: #246bb5;
    --panel-blue: #7097c0;
    --rule-dark: #2a2a2a;
    --ink: #1e1e1e;
    --white: #ffffff;
  }
  * { margin: 0; padding: 0; box-sizing: border-box; }
  html, body {
    width: 1200px; height: 1097px; overflow: hidden;
    background: var(--page);
    font-family: "Source Sans 3", "Helvetica Neue", Arial, sans-serif;
  }
  .canvas { position: relative; width: 1200px; height: 1097px; }

  .card {
    position: absolute;
    width: 811px; height: 462px;
    background: var(--card-grey);
    border: 1px solid #9a9a9a;
    overflow: hidden;
  }
  .card--front { left: 63px; top: 65px; }
  .card--back  { left: 333px; top: 581px; }

  /* front */
  .brand {
    position: absolute; left: 0; right: 0; top: 150px;
    display: flex; flex-direction: column; align-items: center; gap: 4px;
    font-family: "Titillium Web", "Arial Narrow", sans-serif;
    font-weight: 700; color: var(--brand-blue);
    text-transform: uppercase; line-height: 1;
  }
  .brand__row { display: flex; align-items: center; gap: 16px; }
  .brand__mark { width: 40px; height: 40px; background: var(--brand-blue); }
  .brand__name { font-size: 64px; letter-spacing: 1px; }
  .brand__tagline { font-size: 34px; letter-spacing: 0.5px; }

  .divider {
    position: absolute; left: 0; right: 0; top: 308px;
    height: 4px; background: var(--rule-dark);
  }
  .contact-band {
    position: absolute; left: 0; right: 0; top: 312px; bottom: 0;
    background: var(--brand-blue);
    display: flex; flex-direction: column; align-items: center;
    padding-top: 30px; gap: 10px;
    color: var(--white); font-size: 23px; line-height: 25px;
  }
  .contact-line { display: flex; align-items: center; gap: 8px; }
  .contact-line svg { width: 18px; height: 18px; flex: none; }

  /* back */
  .services {
    position: absolute; left: 35px; top: 194px;
    width: 740px; height: 167px;
    background: var(--panel-blue); border-radius: 18px;
    color: var(--white); text-align: center;
  }
  .services__title {
    margin-top: 20px;
    font-size: 31px; font-weight: 700; letter-spacing: 3.5px;
  }
  .services__list { list-style: none; margin-top: 14px; font-size: 26px; font-weight: 600; line-height: 37px; }
  .services__list li span + span::before { content: "• "; margin-left: 8px; }
  .services__list li span:first-child::before { content: "• "; }

  .web-address {
    position: absolute; left: 0; right: 0; top: 402px;
    text-align: center; font-size: 28px; letter-spacing: 2.5px; color: var(--ink);
  }
</style>
</head>
<body>
<main class="canvas">

  <section class="card card--front" aria-label="Business card front">
    <div class="brand">
      <div class="brand__row">
        <span class="brand__mark" aria-hidden="true"></span>
        <span class="brand__name">Brightway Haul</span>
      </div>
      <span class="brand__tagline">&amp; Upkeep Services</span>
    </div>

    <div class="divider"></div>

    <div class="contact-band">
      <p class="contact-line">
        <svg viewBox="0 0 20 20" aria-hidden="true"><circle cx="10" cy="10" r="8.5" fill="none" stroke="#fff" stroke-width="1.5"/><path d="M7 5.5c-1 1-1 3 .8 5.4s4 3.6 5.3 3.2l1-1.3-2-1.5-1 .8c-1-.5-2.1-1.8-2.5-2.8l.8-1-1.3-2.1z" fill="#fff"/></svg>
        0487650392
      </p>
      <p class="contact-line">
        <svg viewBox="0 0 20 20" aria-hidden="true"><g fill="none" stroke="#fff" stroke-width="1.3"><circle cx="10" cy="10" r="8"/><ellipse cx="10" cy="10" rx="3.5" ry="8"/><path d="M2 10h16M3.5 6h13M3.5 14h13"/></g></svg>
        www.brightwayhaul.com.au
      </p>
      <p class="contact-line">
        <svg viewBox="0 0 20 20" aria-hidden="true"><path d="M2 8l8-5 8 5v9H2z" fill="#fff"/><path d="M2 8l8 5 8-5" fill="none" stroke="#246bb5" stroke-width="1.5"/></svg>
        brightwayhaulandupkeep@mailbox.example
      </p>
    </div>
  </section>

  <section class="card card--back" aria-label="Business card back">
    <div class="services">
      <h2 class="services__title">Services we offer</h2>
      <ul class="services__list">
        <li><span>CLEAN</span><span>MOVE</span></li>
        <li><span>GENERAL MAINTENANCE AND REPAIRS.</span></li>
      </ul>
    </div>
    <p class="web-address">www.brightwayhaul.com.au</p>
  </section>

</main>
</body>
</html>
```